A Small Coastal town of New Zealand book!

we want a cool book cover for our book titled; Wharepuke Bay & Its Hidden Western Coves - Old Stories, Diving, Tramping and places to see...

attached are some screenshots of books we found that were similar to the topic i cover.

also attached are some screenshots of some ideas i have been playing with my self with myself on canva...

i quite like the first one how he managed to put 5 images there without making it look too busy...

Tourists

Tourism

Serif
Sans Serif

• Nice coastal image and good fonts and text placement
• not to busy...

```html
<!DOCTYPE html>
<html lang="en">
<head>
<meta charset="utf-8">
<title>Wharepuke Bay – Book Cover</title>
<link href="https://fonts.googleapis.com/css2?family=Playfair+Display:ital,wght@0,400;1,400;1,700&family=Libre+Baskerville:ital,wght@0,400;1,400;1,700&display=swap" rel="stylesheet">
<style>
  :root {
    --sea-top: #0f9fb0;
    --sea-mid: #16a9b9;
    --shore: #6fa8a0;
    --forest: #7b9240;
    --forest-deep: #4f6a2a;
    --ink: #14202a;
    --white: #ffffff;
    --rule: #e4ddcf;
    --band: rgba(20, 110, 120, 0.55);
    --tag-solid: rgba(226, 236, 238, 0.88);
    --tag-soft: rgba(255, 255, 255, 0.58);
  }
  * { margin: 0; padding: 0; box-sizing: border-box; }
  html, body { width: 759px; height: 1200px; overflow: hidden; background: #fff; }

  .cover {
    position: relative;
    width: 759px;
    height: 1200px;
    overflow: hidden;
  }

  .cover-photo {
    position: absolute;
    inset: 0;
    background:
      radial-gradient(ellipse 70% 55% at 55% 100%, var(--forest) 0%, var(--forest) 55%, rgba(123,146,64,0) 75%),
      linear-gradient(180deg, var(--sea-top) 0%, var(--sea-mid) 45%, var(--shore) 70%, var(--forest-deep) 100%);
  }

  .rule {
    position: absolute;
    left: 283px;
    width: 167px;
    height: 4px;
    background: var(--rule);
  }
  .rule--top { top: 65px; }
  .rule--bottom { top: 1156px; }

  .title {
    position: absolute;
    top: 78px;
    left: 0;
    width: 759px;
    text-align: center;
    font-family: "Playfair Display", serif;
    font-style: italic;
    font-weight: 400;
    font-size: 100px;
    line-height: 1.2;
    letter-spacing: 2px;
    color: var(--white);
  }

  .subtitle {
    position: absolute;
    top: 227px;
    left: 78px;
    width: 592px;
    height: 57px;
    background: var(--band);
    display: flex;
    align-items: center;
    justify-content: center;
    font-family: "Libre Baskerville", serif;
    font-style: italic;
    font-size: 25px;
    color: var(--white);
    letter-spacing: -0.3px;
  }

  .tag {
    position: absolute;
    display: flex;
    align-items: center;
    justify-content: center;
    font-family: "Libre Baskerville", serif;
    font-style: italic;
    font-weight: 700;
    font-size: 24px;
    letter-spacing: 3px;
    color: var(--ink);
  }
  .tag--history { top: 358px; left: 229px; width: 285px; height: 70px; background: var(--tag-solid); }
  .tag--diving  { top: 585px; left: 229px; width: 285px; height: 70px; background: var(--tag-soft); }
  .tag--places  { top: 811px; left: 197px; width: 367px; height: 69px; background: var(--tag-soft); }

  .author-credit {
    position: absolute;
    top: 950px;
    left: 0;
    width: 759px;
    text-align: center;
    font-family: "Libre Baskerville", serif;
    font-size: 16px;
    letter-spacing: 14px;
    color: var(--white);
  }

  .author-name {
    position: absolute;
    top: 982px;
    left: 0;
    width: 759px;
    text-align: center;
    font-family: "Playfair Display", serif;
    font-style: italic;
    font-weight: 400;
    font-size: 72px;
    line-height: 62px;
    color: var(--white);
  }
</style>
</head>
<body>
  <main class="cover">
    <div class="cover-photo" role="img" aria-label="Aerial photograph of a tree-covered coastal peninsula with a winding road and small jetty, surrounded by turquoise water"></div>

    <div class="rule rule--top"></div>
    <h1 class="title">Wharepuke</h1>
    <p class="subtitle">Bay &amp; Its Hidden Western Coves</p>

    <p class="tag tag--history">old stories</p>
    <p class="tag tag--diving">diving</p>
    <p class="tag tag--places">and places to see</p>

    <p class="author-credit">BEST SELLING AUTHOR</p>
    <p class="author-name">Corin<br>Halvey</p>
    <div class="rule rule--bottom"></div>
  </main>
</body>
</html>
```